RW Holloway LLC Business Card - Civil Engineering & Consulting Firm

We need a Business Card that is elegant, and masculine.  It is our Professional Civil Engineering & Consulting Company located in San Antonio TX (Not s construction or builder firm- no gears & no tool images please). We provide civil engineering services including  commercial site plans, grading and drainage plans, utility plans, hydraulics and hydrology, land planning, utility coordination, and other general civil engineering services related to commercial and residential development.
We have 2 existing Logos. We would like to convey reliability, strength, trustworthiness and attention to detail.  Blues and orange tones as per logo We are OK with the use of a darker blue in the mix.  We have 2 logo versions - Full Company Name Logo to go on the back of card, & Small Icon Logo for the front w/ personal Info.

Target Market(s)
Architects, Real Estate Developers, Other Strctural Engineers, Surveyers, General Contractors
Industry/Entity Type
Professional Civil Engineering
Contact Information for Business Card
Name, Position, Address, Cell & Office #, email, and company website
Font styles to use
Other font styles liked:
- Avian
Requirements
Should not have
- No Tools, No Gears, no Cranes, or Construction Equipment.

```html
<!DOCTYPE html>
<html lang="en">
<head>
<meta charset="utf-8">
<title>RW Holloway LLC Business Card</title>
<link rel="stylesheet" href="https://fonts.googleapis.com/css2?family=Josefin+Sans:wght@300;400&family=Arimo:wght@400&display=swap">
<style>
  :root {
    --bg: #3b3b3d;
    --card-white: #ffffff;
    --brand-blue: #7aabd7;
    --brand-orange: #f39321;
    --ink: #1d1d1f;
    --rule: #b9b9b9;
  }
  * { margin: 0; padding: 0; box-sizing: border-box; }
  html, body { width: 1200px; height: 866px; overflow: hidden; background: var(--bg); }
  .canvas { position: relative; width: 1200px; height: 866px; }
  .card {
    position: absolute; top: 278px; width: 540px; height: 309px;
    overflow: hidden; box-shadow: 0 10px 24px rgba(0,0,0,.45);
  }
  .card--front { left: 40px; background: var(--card-white); }
  .card--back { left: 620px; background: var(--brand-blue); }

  .person { position: absolute; left: 32px; top: 40px; width: 180px; }
  .person__name {
    font-family: "Josefin Sans", sans-serif; font-weight: 300; font-size: 21px;
    letter-spacing: 1px; color: var(--brand-blue); white-space: nowrap;
  }
  .person__name .surname { color: var(--brand-orange); font-weight: 400; }
  .person__title { font-family: "Arimo", sans-serif; font-size: 13px; color: var(--ink); margin-top: 2px; }
  .contact { margin-top: 12px; font-family: "Arimo", sans-serif; font-size: 12.5px; color: var(--ink); }
  .contact__row { display: flex; align-items: center; gap: 7px; margin-bottom: 4px; }
  .contact__row svg { width: 12px; height: 12px; flex: none; }

  .wordmark { position: absolute; text-align: left; }
  .wordmark__name {
    display: flex; align-items: center; gap: 10px;
    font-family: "Josefin Sans", sans-serif; font-weight: 300; letter-spacing: 3px;
    white-space: nowrap;
  }
  .wordmark__mark { flex: none; }
  .wordmark__tag {
    font-family: "Josefin Sans", sans-serif; font-weight: 300; letter-spacing: 4px;
    border-top: 1px solid currentColor; padding-top: 5px; margin-top: 5px; white-space: nowrap;
  }
  .card--front .wordmark { right: 30px; top: 88px; }
  .card--front .wordmark__name { font-size: 22px; letter-spacing: 2.5px; color: var(--brand-blue); }
  .card--front .wordmark__mark { width: 12px; height: 12px; background: var(--brand-orange); }
  .card--front .wordmark__tag { font-size: 9px; color: var(--brand-orange); border-top-color: var(--brand-blue); }

  .divider { position: absolute; left: 32px; right: 30px; top: 172px; border-top: 1px solid var(--rule); }
  .address {
    position: absolute; right: 36px; top: 184px; text-align: right; font-style: normal;
    font-family: "Arimo", sans-serif; font-size: 13px; line-height: 1.35; color: var(--ink);
  }
  .band { position: absolute; left: 0; bottom: 0; width: 540px; height: 66px; }
  .website {
    position: absolute; right: 36px; bottom: 14px;
    font-family: "Arimo", sans-serif; font-size: 13px; letter-spacing: .5px; color: #fff;
  }

  .card--back .wordmark { left: 50%; top: 50%; transform: translate(-50%, -50%); }
  .card--back .wordmark__name { font-size: 34px; color: #fff; }
  .card--back .wordmark__mark { width: 18px; height: 18px; background: #fff; }
  .card--back .wordmark__tag { font-size: 11px; color: #fff; text-align: center; }
</style>
</head>
<body>
<main class="canvas">
  <section class="card card--front" aria-label="Business card front">
    <div class="person">
      <p class="person__name">MARCUS <span class="surname">REED</span></p>
      <p class="person__title">Managing Director</p>
      <div class="contact">
        <p class="contact__row">
          <svg viewBox="0 0 12 12" aria-hidden="true"><path d="M3 1 L5 3.5 L4 5 Q5 7 7 8 L8.5 7 L11 9 L9.5 11 Q4 10.5 1 3 Z" fill="var(--brand-blue)"/></svg>
          044-210 387 654
        </p>
        <p class="contact__row">
          <svg viewBox="0 0 12 12" aria-hidden="true"><rect x="0.5" y="2.5" width="11" height="7.5" fill="var(--brand-blue)"/><path d="M0.5 2.5 L6 7 L11.5 2.5" fill="none" stroke="#fff" stroke-width="1"/></svg>
          info@hollowayce.com
        </p>
      </div>
    </div>

    <div class="wordmark">
      <p class="wordmark__name"><span class="wordmark__mark"></span>RW HOLLOWAY LLC</p>
      <p class="wordmark__tag">CONSULTING ENGINEERS</p>
    </div>

    <div class="divider"></div>
    <address class="address">1850, Riverbend Road Suite 4<br>78205, San Antonio TX</address>

    <svg class="band" viewBox="0 0 540 66" aria-hidden="true">
      <path d="M0 14 L225 14" stroke="var(--brand-orange)" stroke-width="5"/>
      <path d="M0 24 L228 24 C252 24 258 10 290 10 L540 10 L540 66 L0 66 Z" fill="var(--brand-blue)"/>
      <path d="M0 19 L225 19" stroke="#fff" stroke-width="2"/>
    </svg>
    <p class="website">www.hollowayce.com</p>
  </section>

  <section class="card card--back" aria-label="Business card back">
    <div class="wordmark">
      <p class="wordmark__name"><span class="wordmark__mark"></span>RW HOLLOWAY LLC</p>
      <p class="wordmark__tag">CONSULTING ENGINEERS</p>
    </div>
  </section>
</main>
</body>
</html>
```